Commercial Real Estate for Lease Listing Flyer

I am looking to put together a flyer for our available office space in our building. It needs to look professional and it will be standard sized 8.5 x 11 and double sided. Full color as well. This flyer will need to be able to be put in a PDF and a picture file that can be embedded in an email. I have included pictures, logo, and a Word document with the information you should need. Also, I included a bunch of SAMPLE leasing flyers that you can get ideas from. The floor plan is also included in here. I want it specifically noted that the top suite is Suite 100 and the bottom suite is 120. And list their size as well. I will be reviewing all designs very quickly, so be sure to check the comments.

• Please refer to these links for additional photos:
• "Twilight 1.jpg" at: https://files.plinthdocs.net/a/preview/3f7d1a92-b4e0-4c1a-8e5f-71c0d2ab9e34
• Twilight 2_straightened.jpg" at: https://files.plinthdocs.net/a/preview/a15c8e03-7d2b-4f9e-b6a1-0c93e4f72d58
• "Twilight 3.jpg" at: https://files.plinthdocs.net/a/preview/6e2b9f71-c3a4-4d08-9e7b-5f1a8c03d6e2
• "Twilight 4.jpg" at: https://files.plinthdocs.net/a/preview/c84a0d6e-1f3b-4e57-a2c9-9b7e05f4d813
• "Twilight 5.jpg" at: https://files.plinthdocs.net/a/preview/7b0f5c28-e6d1-4a93-8f4e-d25a1b6c07f9
• "Twilight 6.jpg" at: https://files.plinthdocs.net/a/preview/e3c6a417-5b92-4f0d-bc8e-4a1f97d2e065
• "Twilight 7.jpg" at: https://files.plinthdocs.net/a/preview/5a9d2e80-c7f4-4b16-93a0-e8b6f1c4d27a
• "Twilight 8.jpg" at: https://files.plinthdocs.net/a/preview/b2e7f069-84c3-4d5a-a71e-3c0d9b58f6e4
• "Twilight 9.jpg" at: https://files.plinthdocs.net/a/preview/4d8c1b3f-a0e5-4f72-8b69-f17e2c05a9d3
• "Twilight 10.jpg" at: https://files.plinthdocs.net/a/preview/f09a6c52-3e18-4b7d-9c24-6b5d80e1f3a7
• "Twilight 11.jpg" at: https://files.plinthdocs.net/a/preview/8e4f2d06-b9c7-4a31-85e0-d7a3c16f4b92

```html
<!DOCTYPE html>
<html lang="en">
<head>
<meta charset="utf-8">
<title>Harbor Road Centre – Leasing Flyer</title>
<link href="https://fonts.googleapis.com/css2?family=Montserrat:wght@400;600;700&family=Roboto:wght@300;400&display=swap" rel="stylesheet">
<style>
:root{
  --bg:#e4e5e6;
  --charcoal:#363334;
  --gold:#c9a867;
  --gold-deep:#b08f4e;
  --sand:#e3d39c;
  --brown:#5e4a36;
  --ink:#4a4440;
  --orange:#e8772e;
  --blue:#1f7fc0;
  --navy:#1d3f7a;
  --white:#ffffff;
}
*{box-sizing:border-box;margin:0;padding:0}
html,body{width:1200px;height:1200px;overflow:hidden}
body{background:var(--bg);position:relative;font-family:"Roboto",sans-serif}
.page{position:absolute;width:553px;height:715px;background:var(--white);overflow:hidden;box-shadow:0 3px 10px rgba(0,0,0,.18)}
.page--front{left:29px;top:19px}
.page--back{left:604px;top:437px}
.photo{position:absolute}
.photo--entry{left:0;top:0;width:276px;height:155px;background:linear-gradient(160deg,#d2b27f,#8f7a58 60%,#4d5a3a)}
.photo--drive{left:277px;top:0;width:276px;height:155px;background:linear-gradient(180deg,#8e8fc2,#b7a3b8 40%,#4f6a3d 70%,#55595e)}
.title-band{position:absolute;left:0;top:155px;width:553px;height:145px;background:var(--charcoal);font-family:"Montserrat",sans-serif}
.title{position:absolute;left:0;right:0;top:8px;text-align:center;color:var(--gold);font-weight:700;font-size:41px;line-height:48px;letter-spacing:.3px;white-space:nowrap}
.address{position:absolute;left:79px;width:404px;top:62px;height:33px;line-height:31px;text-align:center;color:#f1ede6;font-size:16px;font-weight:400;white-space:nowrap;border-top:1px solid #8a7f70;border-bottom:1px solid #8a7f70}
.tagline{position:absolute;left:0;right:0;top:110px;line-height:18px;text-align:center;color:#fff;font-weight:700;font-size:14.5px;letter-spacing:.8px;white-space:nowrap}
.photo--hero{left:0;top:300px;width:553px;height:282px;background:linear-gradient(175deg,#8c8dc7,#c3a8bd 25%,#c9a872 45%,#4d6a37 75%,#5b5f63)}
.thumbs{position:absolute;left:0;top:584px;width:553px;height:99px;display:flex;gap:3px}
.thumb{flex:1;background:linear-gradient(160deg,#c7ae74,#9b7f52 60%,#5a4632)}
.front-footer{position:absolute;left:0;top:683px;width:553px;height:32px;font-family:"Montserrat",sans-serif;font-size:10.5px;color:#6b6b6b;display:flex;align-items:center;justify-content:center;gap:4px;white-space:nowrap}
.front-footer b{color:#333}
.front-footer .phone{color:var(--orange);font-weight:700}
.front-footer .mail{color:var(--blue)}
.front-footer .sep{color:#ccc;margin:0 4px}

.info-col{position:absolute;left:0;top:0;width:310px;height:631px;background:var(--sand)}
.plan{position:absolute;left:8px;top:31px;width:326px;height:263px;background:#fff;border-radius:16px;box-shadow:0 1px 6px rgba(0,0,0,.2);z-index:2;display:flex;align-items:center;justify-content:center}
.plan-fill{width:286px;height:220px;background:linear-gradient(135deg,#f4f4f4,#dcdcdc)}
.highlights{position:absolute;left:32px;top:336px;width:262px;list-style:none;font-size:12px;line-height:16px;color:var(--ink);font-weight:300}
.highlights li{padding:6px 0 8px;border-bottom:1px solid var(--gold-deep)}
.highlights li:last-child{border-bottom:none}
.spec-col{position:absolute;left:310px;top:0;width:243px;height:631px;background:var(--brown);font-family:"Montserrat",sans-serif}
.curl{position:absolute;left:0;top:0}
.rent{position:absolute;right:10px;top:20px;text-align:right;color:var(--brown);font-weight:700;line-height:1}
.rent-line{display:flex;align-items:center;justify-content:flex-end;gap:2px}
.rent-label{font-size:10px;letter-spacing:.5px}
.rent-amount{font-size:24px}
.rent-unit{font-size:9px;text-align:left}
.rent-note{font-size:11px;margin-top:7px;letter-spacing:.4px}
.suite{position:absolute;left:38px;width:200px;color:#efe6d4;font-size:9.6px;line-height:12px;white-space:nowrap}
.suite h3{display:inline;color:var(--gold);font-size:15px;font-weight:600}
.suite--100{top:160px}
.suite--120{top:236px}
.combined{position:absolute;left:38px;top:302px;color:var(--gold);font-size:12.5px;font-weight:600;line-height:17px;white-space:nowrap}
.features-title{position:absolute;left:38px;top:366px;color:var(--gold);font-size:20px;font-weight:700;line-height:19px}
.features{position:absolute;left:38px;top:412px;width:185px;list-style:none;color:#fff;font-size:9.4px;font-weight:700;line-height:12px}
.features li{padding:3px 0 9px;margin-bottom:5px;border-bottom:1px solid var(--gold-deep)}
.features li:last-child{border-bottom:none}
.back-footer{position:absolute;left:0;top:631px;width:553px;height:84px;background:#fff;font-family:"Montserrat",sans-serif}
.brand{position:absolute;left:36px;top:26px;width:120px;color:var(--navy);font-size:15px;font-weight:600;letter-spacing:1.5px;line-height:17px;text-align:center}
.lease-contact{position:absolute;left:167px;top:33px;width:160px;color:var(--gold-deep);font-size:10px;font-weight:600;line-height:13px;white-space:nowrap}
.lease-contact b{color:var(--navy)}
.contact-block{position:absolute;right:26px;top:20px;width:170px;text-align:center}
.contact-phone{color:var(--gold-deep);font-size:24px;font-weight:700;line-height:28px;white-space:nowrap}
.contact-mail{background:var(--navy);color:#fff;font-size:10.5px;padding:2px 0;margin-top:2px;white-space:nowrap}
</style>
</head>
<body>

<section class="page page--front">
  <div class="photo photo--entry" role="img" aria-label="Arched entrance of the office building"></div>
  <div class="photo photo--drive" role="img" aria-label="Driveway and building at twilight"></div>
  <header class="title-band">
    <h1 class="title">Harbor Road Centre</h1>
    <p class="address">4180 Harbor Road, Palm Grove Gardens, FL 33400</p>
    <p class="tagline">CLASS A OFFICE SPACE AVAILABLE FOR LEASE</p>
  </header>
  <div class="photo photo--hero" role="img" aria-label="Building exterior with palm trees at twilight"></div>
  <div class="thumbs">
    <div class="thumb" role="img" aria-label="Private office with desk and arched window"></div>
    <div class="thumb" role="img" aria-label="Conference room with table and chairs"></div>
    <div class="thumb" role="img" aria-label="Office with wooden door"></div>
    <div class="thumb" role="img" aria-label="Executive office with desk"></div>
  </div>
  <footer class="front-footer">
    For more information, please contact : <b>Brent Solano</b> @ <span class="phone">561-555-0142</span><span class="sep">|</span><span class="mail">brent@solanocompanies.com</span>
  </footer>
</section>

<section class="page page--back">
  <div class="info-col">
    <ul class="highlights">
      <li>The Harbor Road Centre is a beautiful Class A building situation in the heart of Palm Grove Gardens but without the Boulevard traffic.</li>
      <li>Harbor Road Centre is located directly<br>on I-95 just off of Harbor Road.</li>
      <li>The new Linden development south<br>entrance is being built across the street.</li>
      <li>The suites are incredibly well appointed and move-in ready with custom oak doors and millwork, 10' ceilings, floor to ceiling windows</li>
      <li>The building is very convenient to restaurants, shopping &amp; every other trade needed.</li>
    </ul>
  </div>
  <div class="plan"><div class="plan-fill" role="img" aria-label="Floor plan of Suite 100 and Suite 120"></div></div>
  <div class="spec-col">
    <svg class="curl" width="243" height="165" viewBox="0 0 243 165" aria-hidden="true">
      <path d="M82 0H243V160Q165 118 120 70Q92 35 82 0Z" fill="#c9a867"/>
      <path d="M82 0Q92 35 120 70Q165 118 243 160L243 163Q150 128 110 80Q140 95 95 40Q84 20 82 0Z" fill="#f2f2f2"/>
    </svg>
    <div class="rent">
      <div class="rent-line"><span class="rent-label">RENTAL<br>RATE</span><span class="rent-amount">$32</span><span class="rent-unit">/SF<br>All in</span></div>
      <div class="rent-note">NO EXTRA<br>OPERATING<br>EXPENSES</div>
    </div>
    <div class="suite suite--100"><h3>Suite 100</h3> 2,303 SF Available<br>in February 2019 or earlier.<br>6 offices, break room,<br>reception area, conference room,<br>and a large meeting room.</div>
    <div class="suite suite--120"><h3>Suite 120</h3> 1,488 SF Available Now.<br>2-3 offices, 1 large executive office,<br>conference room, break room<br>and reception area.</div>
    <p class="combined">Both suites can be combined<br>for 3,791 SF in total.</p>
    <h2 class="features-title">FEATURES<br>&amp; AMENITIES</h2>
    <ul class="features">
      <li>Completely move-in ready<br>Change On site management to</li>
      <li>Floor-to-ceiling hurricane<br>impact windows throughout</li>
      <li>Plenty of parking</li>
      <li>On-site management</li>
      <li>On site ownership and management</li>
      <li>Some furniture available if needed</li>
    </ul>
  </div>
  <footer class="back-footer">
    <div class="brand">SOLANO<br>COMPANIES</div>
    <p class="lease-contact">For leasing information,<br>please contact : <b>Brent Solano</b></p>
    <div class="contact-block">
      <div class="contact-phone">561-555-0142</div>
      <div class="contact-mail">brent@solanocompanies.com</div>
    </div>
  </footer>
</section>

</body>
</html>
```